Brimora - Nutritious Snacks and Desserts

We need a creative e-commerce website in which all features--buttons, background, etc.--convey our message: We sell delicious, nutritious snacks and desserts that most closely comply with the paleo diet guidelines. Our first product is Nuttaree®--raw, vegan, paleo chocolate balls that are made of dates, coconut, and cocoa. Our products are organic, raw, irresistible and nutritious. We have several versions of Nuttaree® in development, as well as mousse, ice cream, and crackers. Our mission is to purvey basic healthy foods. Our motto is, "Fuel for the Bold Trail-Walker(tm)."

Target Market(s)

Health-conscious professionals who tend to shop at health food stores. Our products also meet the requirements of a gluten-free diet; and they also don't contain refined sugar, so shoppers with gluten and possibly sugar issues are incidental customers.

Industry/Entity Type

Health Product

Coding

Number of Pages Required

5+ page

Colors

Designer to choose colors to be used in the design.

Requirements
Must have
• We need at least a home page, a products page, an about-us page, a contact page, and a shopping cart page. We would like to be able to add products on our own later. We should be able to handle some basic coding, especially if it's just a matter of copying and modifying product pages. We would also like the ability in the future to add blogging pages, allowing us to write articles about health food and healthy lifestyle, thus attracting web-traffic (SEO).
• Other features we would like to have:
• Product photo slider on the hopepage
• Back-to-top button at the bottom of the home page
• Make sure the site is mobile-compatible
• A search bar at the top of the homepage
• "Create an account" and "Previous orders"--allowing customers to see their previous orders and reorder what they purchased in the past.
Nice to have
• We would like to convey the paleo theme without actually stating it anywhere. We'll add text as necessary, according to the page layout; you can use ipsum lorem for purpose of demonstration.

```html
<!DOCTYPE html>
<html lang="en">
<head>
<meta charset="utf-8">
<title>Brimora – Nutritious Snacks and Desserts</title>
<link href="https://fonts.googleapis.com/css2?family=Lato:wght@400;700&family=Parisienne&family=Caveat:wght@400;500&family=Merriweather:wght@400&display=swap" rel="stylesheet">
<style>
:root{
  --leaf:#7dc60b;
  --leaf-deep:#3f6410;
  --button:#4b7a05;
  --lime:#c9e21a;
  --charcoal:#555657;
  --charcoal-top:rgba(70,70,72,.85);
  --ink:#ffffff;
  --grey-text:#8a8a8a;
  --body-text:#555555;
  --hero-a:#fbeef3;
  --hero-b:#f2efe9;
}
*{margin:0;padding:0;box-sizing:border-box}
html,body{width:1200px;height:2242px;overflow:hidden;background:#fff}
body{position:relative;font-family:"Lato",sans-serif;color:var(--body-text)}
.abs{position:absolute}

/* header */
.site-header{position:absolute;left:0;top:0;width:1200px;height:84px;background:var(--charcoal-top);z-index:5}
.main-nav a{position:absolute;top:29px;font-size:17px;color:var(--lime);text-decoration:none}
.main-nav a.is-active{color:var(--ink)}
.cart-icon{position:absolute;left:1088px;top:20px}
.brand{position:absolute;left:74px;top:26px;width:210px;text-align:center;z-index:6}
.brand-mark{width:108px;height:108px;margin:0 auto;border-radius:50%;background:var(--leaf);border:7px solid #fff}
.brand-name{font-weight:700;font-size:42px;color:var(--leaf);letter-spacing:3px;line-height:1;margin-top:8px}

/* hero */
.hero-photo{position:absolute;left:0;top:84px;width:1200px;height:560px;
  background:radial-gradient(ellipse at 55% 40%,#e6ddcf 0%,rgba(230,221,207,0) 45%),
             radial-gradient(ellipse at 15% 25%,#f6d6e3 0%,rgba(246,214,227,0) 40%),
             radial-gradient(ellipse at 85% 70%,#f3cfd4 0%,rgba(243,207,212,0) 35%),
             linear-gradient(135deg,var(--hero-a),var(--hero-b))}
.hero-title{position:absolute;left:0;top:262px;width:1200px;text-align:center;font-family:"Parisienne",cursive;font-size:118px;line-height:134px;color:var(--leaf-deep)}

/* products */
.products-band{position:absolute;left:0;top:640px;width:1200px;height:548px;background:var(--leaf)}
.torn{position:absolute;left:0;width:1200px}
.section-script{font-family:"Caveat",cursive;font-weight:400;line-height:1}
.products-title{position:absolute;left:0;top:690px;width:1200px;text-align:center;font-size:82px;color:var(--ink)}
.product-card{position:absolute;top:822px;width:250px;text-align:center;color:var(--ink)}
.product-photo{width:190px;height:190px;margin:0 auto;border-radius:50%;
  background:radial-gradient(circle at 45% 40%,#d9c8ad 0%,#9c7a55 55%,#5b3b22 100%)}
.product-name{font-weight:700;font-size:18px;margin-top:24px}
.product-text{font-size:13.5px;line-height:19px;margin-top:12px;opacity:.92}

/* welcome */
.welcome-photo{position:absolute;left:0;top:1196px;width:1200px;height:502px;
  background:radial-gradient(ellipse at 88% 35%,#f68cb8 0%,rgba(246,140,184,0) 22%),
             radial-gradient(ellipse at 85% 55%,#f4c872 0%,rgba(244,200,114,0) 22%),
             linear-gradient(180deg,#ffffff 0%,#fbfbfb 72%,#f3e6ec 88%,#f6eef0 100%)}
.welcome-title{position:absolute;left:78px;top:1326px;font-size:74px;color:var(--leaf-deep)}
.welcome-copy{position:absolute;left:79px;top:1428px;width:560px;font-size:17px;line-height:25px;color:var(--grey-text)}
.welcome-copy p+p{margin-top:16px}

/* newsletter */
.newsletter-title{position:absolute;left:0;top:1752px;width:1200px;text-align:center;font-size:74px;color:var(--leaf-deep)}
.newsletter-sub{position:absolute;left:0;top:1846px;width:1200px;text-align:center;font-size:16px;color:var(--body-text)}
.email-field{position:absolute;left:291px;top:1890px;width:455px;height:50px;border:1px solid #a9a9a9;border-radius:3px;font-size:10px;color:#aaa;padding:8px 16px}
.subscribe-btn{position:absolute;left:753px;top:1890px;width:156px;height:50px;background:var(--button);color:#fff;font-size:20px;line-height:50px;text-align:center;border-radius:2px}

/* footer */
.site-footer{position:absolute;left:0;top:2000px;width:1200px;height:242px;background:var(--charcoal)}
.footer-heading{position:absolute;top:2042px;font-family:"Merriweather",serif;font-size:22px;color:var(--lime)}
.footer-line{position:absolute;left:122px;font-size:14px;line-height:23px;color:#fff}
.footer-icon{position:absolute;left:78px}
.footer-mark{position:absolute;left:534px;top:2028px;width:132px;height:132px;border-radius:50%;background:var(--leaf);border:6px solid #b7e04a;
  color:#fff;font-weight:700;font-size:26px;line-height:120px;text-align:center}
.copyright{position:absolute;left:0;top:2198px;width:1200px;text-align:center;font-size:14px;color:#fff}
.copyright .name{color:var(--lime)}
.quick-link{position:absolute;font-size:14px;color:#fff;text-decoration:none}
</style>
</head>
<body>

<header class="site-header">
  <nav class="main-nav">
    <a class="is-active" href="#" style="left:571px">Home</a>
    <a href="#" style="left:705px">About</a>
    <a href="#" style="left:830px">Product</a>
    <a href="#" style="left:968px">Contact Us</a>
  </nav>
  <svg class="cart-icon" width="36" height="42" viewBox="0 0 36 42" aria-label="Cart, 0 items">
    <path d="M11 12 V8 a7 7 0 0 1 14 0 V12" fill="none" stroke="#c9e21a" stroke-width="2"/>
    <rect x="3" y="12" width="30" height="27" fill="none" stroke="#c9e21a" stroke-width="2"/>
    <text x="18" y="32" text-anchor="middle" font-family="Lato, sans-serif" font-size="17" fill="#fff">0</text>
  </svg>
</header>

<div class="brand">
  <div class="brand-mark"></div>
  <div class="brand-name">brimora</div>
</div>

<section class="hero">
  <div class="hero-photo" role="img" aria-label="Soft-focus photo of a glazed marble bundt cake slice with strawberries and pink blossoms"></div>
  <h1 class="hero-title">Delicious Nutritious<br>Snacks and Desserts</h1>
</section>

<section class="products">
  <div class="products-band"></div>
  <svg class="torn" style="top:616px" height="40" viewBox="0 0 1200 40" preserveAspectRatio="none">
    <polygon fill="#7dc60b" points="0,40 0,18 30,22 55,14 90,20 120,12 160,18 200,10 240,17 275,12 320,19 360,11 400,16 445,9 490,17 530,12 570,18 610,10 650,16 700,11 740,18 780,9 830,15 870,12 910,18 950,8 1000,15 1040,11 1080,17 1120,7 1160,14 1200,10 1200,40"/>
  </svg>
  <svg class="torn" style="top:1180px" height="40" viewBox="0 0 1200 40" preserveAspectRatio="none">
    <polygon fill="#7dc60b" points="0,0 1200,0 1200,14 1170,22 1140,16 1100,26 1060,18 1020,24 980,15 940,23 900,17 860,27 820,19 780,25 740,16 700,24 660,18 620,28 580,20 540,26 500,17 460,25 420,19 380,28 340,20 300,26 260,18 220,27 180,19 140,25 100,17 60,26 30,20 0,24"/>
  </svg>
  <h2 class="products-title section-script">products</h2>

  <article class="product-card" style="left:77px">
    <div class="product-photo" role="img" aria-label="Product tub with chocolate squares and pecans"></div>
    <h3 class="product-name">Lorem ipsum text.</h3>
    <p class="product-text">Lorem ipsum dolor sit amet<br>consect etur adipiscing elit.<br>Curabitur sempo turpis quis...</p>
  </article>
  <article class="product-card" style="left:343px">
    <div class="product-photo" role="img" aria-label="Round Nuttaree® lid, label Fuel for the Bold Trail-Walker(tm)"></div>
    <h3 class="product-name">Lorem ipsum text.</h3>
    <p class="product-text">Lorem ipsum dolor sit amet<br>consect etur adipiscing elit.<br>Curabitur sempo turpis quis...</p>
  </article>
  <article class="product-card" style="left:607px">
    <div class="product-photo" role="img" aria-label="Product tub with chocolate square and orange slice"></div>
    <h3 class="product-name">Lorem ipsum Dummy text.</h3>
    <p class="product-text">Lorem ipsum dolor sit amet<br>consect etur adipiscing elit.<br>Curabitur sempo turpis quis...</p>
  </article>
  <article class="product-card" style="left:869px">
    <div class="product-photo" role="img" aria-label="Product tub with chocolate squares and orange slice"></div>
    <h3 class="product-name">Lorem ipsum Dummy text.</h3>
    <p class="product-text">Lorem ipsum dolor sit amet<br>consect etur adipiscing elit.<br>Curabitur sempo turpis quis...</p>
  </article>
</section>

<section class="welcome">
  <div class="welcome-photo" role="img" aria-label="Photo of a pink frosted cupcake, piping bag and scattered sprinkles"></div>
  <h2 class="welcome-title section-script">welcome to brimora</h2>
  <div class="welcome-copy">
    <p>Our products are raw, organic, vegan, gluten-free, dairy-free, fiber-rich, nutrient-dense, antioxidant-rich real foods with no preservatives, no added sugar, and no artificial or plant-based sweeteners.</p>
    <p>And they are irresistibly scrumptious!</p>
  </div>
</section>

<section class="newsletter">
  <h2 class="newsletter-title section-script">newsletter</h2>
  <p class="newsletter-sub">Subscribe to our profiles on the following social networks</p>
  <div class="email-field">Enter Your E mail</div>
  <div class="subscribe-btn">SUBSCRIBE</div>
</section>

<footer>
  <div class="site-footer"></div>
  <svg class="torn" style="top:1984px" height="20" viewBox="0 0 1200 20" preserveAspectRatio="none">
    <polygon fill="#555657" points="0,20 0,8 40,12 80,5 120,11 170,4 210,10 260,6 300,12 350,3 400,10 450,5 500,11 550,4 600,9 650,3 700,10 750,5 800,12 850,4 900,9 950,6 1000,12 1050,5 1100,13 1150,8 1200,14 1200,20"/>
  </svg>

  <h4 class="footer-heading" style="left:79px">Contact Us</h4>
  <svg class="footer-icon" style="top:2092px" width="28" height="30" viewBox="0 0 28 30"><path d="M14 27 C6 18 5 14 5 11 a9 9 0 0 1 18 0 c0 3-1 7-9 16z" fill="none" stroke="#fff" stroke-width="2"/><circle cx="14" cy="11" r="3.5" fill="none" stroke="#fff" stroke-width="2"/><path d="M3 28 h22" stroke="#fff" stroke-width="2"/></svg>
  <p class="footer-line" style="top:2082px">123 Building Name, Street Name, Area,<br>City, Country - Zipcode</p>
  <svg class="footer-icon" style="top:2146px" width="24" height="24" viewBox="0 0 24 24"><path d="M5 3 l4 0 2 5 -3 2 c1 3 3 5 6 6 l2-3 5 2 0 4 c-9 1-17-7-16-16z" fill="none" stroke="#fff" stroke-width="1.8" stroke-linejoin="round"/></svg>
  <p class="footer-line" style="top:2146px">123 4567 890</p>
  <svg class="footer-icon" style="top:2190px" width="26" height="20" viewBox="0 0 26 20"><rect x="1" y="1" width="24" height="18" fill="none" stroke="#fff" stroke-width="2"/><path d="M1 1 L13 11 L25 1 M1 19 L10 9 M25 19 L16 9" fill="none" stroke="#fff" stroke-width="2"/></svg>
  <p class="footer-line" style="top:2188px">hello@brimorafoods.com</p>

  <div class="footer-mark">brimora</div>
  <p class="copyright">© <span class="name">brimora</span> - 2018. All Rights Reserved.</p>

  <h4 class="footer-heading" style="left:792px">Quick Link</h4>
  <a class="quick-link" href="#" style="left:802px;top:2084px">Home</a>
  <a class="quick-link" href="#" style="left:802px;top:2111px">About us</a>
  <a class="quick-link" href="#" style="left:802px;top:2138px">Product</a>
  <a class="quick-link" href="#" style="left:802px;top:2164px">Contact Us</a>
  <a class="quick-link" href="#" style="left:949px;top:2084px">My Account</a>
  <a class="quick-link" href="#" style="left:949px;top:2111px">Check out</a>
  <a class="quick-link" href="#" style="left:949px;top:2138px">Track order</a>
  <a class="quick-link" href="#" style="left:949px;top:2164px">Privacy Policy</a>
</footer>

</body>
</html>
```